Brisk Fixwell business card

I need business card for my business, I think you have all my details.six months ago I design with you car wrap design. We would like to design both side of the card. On front of card we would like logo , Name and our contact details.
At the back we are looking to mentioned our services.
The name will be:
Faridoullan Mestor
Managing Director
Ph:07952338417
Email:info@brisk-fixwell.com
Web:www.brisk-fixwell.com
So we have our logo, you don’t need to change the logo.
Please see the attachment.
Thanks

Target Market(s)

Home improvement

Industry/Entity Type

Home Improvement

Contact Information for Business Card

Company name: Brisk Fixwell
Name: Faridoullan Mestor
Position: Director
Ph:07952338417
Web: www.brisk-fixwell.com
Add: 42 Corvale Road
Harrowdene
TW3 9KD
SECOND PERSON
Nizamuddel mestor
Position: Handyman
Ph: 07812 564037
Email: info@brisk-fixwell.com
Add: 18 Brackwin Lane Road
Harrowdene
TW6 2LB

```html
<!DOCTYPE html>
<html lang="en">
<head>
<meta charset="utf-8">
<title>Brisk Fixwell – Business Card</title>
<link rel="stylesheet" href="https://fonts.googleapis.com/css2?family=Open+Sans:wght@400;700;800&display=swap">
<style>
  :root {
    --navy: #263a85;
    --navy-deep: #1f3178;
    --red: #e31d2b;
    --grey-mark: #9a9a9a;
    --grey-text: #4a4a4a;
    --paper: #ffffff;
    --stage: #e6e8ee;
  }
  * { margin: 0; padding: 0; box-sizing: border-box; }
  html, body { width: 1200px; height: 900px; overflow: hidden; }
  body {
    background: var(--stage);
    font-family: "Open Sans", Arial, sans-serif;
    position: relative;
  }
  .card {
    position: absolute;
    left: 250px;
    width: 700px;
    height: 400px;
    overflow: hidden;
    box-shadow: 0 6px 20px rgba(0,0,0,.18);
  }
  .card--front { top: 35px; background: var(--paper); }
  .card--back  { top: 465px; background: var(--navy); }

  /* front */
  .brand {
    position: absolute;
    left: 48px;
    top: 150px;
    display: flex;
    align-items: center;
    gap: 12px;
  }
  .brand__mark {
    width: 22px; height: 22px;
    background: var(--red);
  }
  .brand__name {
    font-weight: 800;
    font-size: 34px;
    color: var(--navy);
    letter-spacing: .5px;
  }
  .divider {
    position: absolute;
    left: 355px;
    top: 80px;
    width: 2px;
    height: 210px;
    background: var(--navy);
  }
  .contact {
    position: absolute;
    left: 385px;
    top: 92px;
    color: var(--grey-text);
    font-size: 17px;
    line-height: 1.45;
  }
  .contact__name {
    font-weight: 800;
    font-size: 24px;
    color: var(--navy);
    line-height: 1.2;
  }
  .contact__role { margin-bottom: 6px; }
  .contact__line {
    display: flex;
    align-items: center;
    gap: 8px;
  }
  .contact__line svg { width: 14px; height: 14px; flex: none; }
  .edge-band {
    position: absolute;
    left: 0; bottom: 0;
    width: 700px; height: 22px;
  }

  /* back */
  .back-brand {
    position: absolute;
    right: 70px;
    bottom: 80px;
    display: flex;
    align-items: center;
    gap: 16px;
  }
  .back-brand__mark {
    width: 30px; height: 30px;
    background: var(--grey-mark);
  }
  .back-brand__name {
    font-weight: 800;
    font-size: 52px;
    color: var(--paper);
    letter-spacing: 1px;
  }
</style>
</head>
<body>

<section class="card card--front" aria-label="Card front">
  <div class="brand">
    <span class="brand__mark"></span>
    <span class="brand__name">Brisk Fixwell</span>
  </div>

  <div class="divider"></div>

  <div class="contact">
    <p class="contact__name">Faridoullan Mestor</p>
    <p class="contact__role">Director</p>
    <p>42 Corvale Road</p>
    <p>Harrowdene, TW3 9KD</p>
    <p class="contact__line">
      <svg viewBox="0 0 16 16" aria-hidden="true"><path fill="#e31d2b" d="M3.5 1.5l2.5 3-1.5 1.6c.8 1.8 2.2 3.2 4 4l1.6-1.5 3 2.5-1.4 2.2C6.5 13.6 2.4 9.5 1.3 2.9z"/></svg>
      07952338417
    </p>
    <p class="contact__line">
      <svg viewBox="0 0 16 16" aria-hidden="true"><rect x="1" y="3" width="14" height="10" fill="#e31d2b"/><path d="M1 3l7 6 7-6" fill="none" stroke="#fff" stroke-width="1.4"/></svg>
      info@brisk-fixwell.com
    </p>
    <p class="contact__line">
      <svg viewBox="0 0 16 16" aria-hidden="true"><circle cx="8" cy="8" r="7" fill="#e31d2b"/><path d="M1 8h14M8 1c-3 3.5-3 10.5 0 14M8 1c3 3.5 3 10.5 0 14" fill="none" stroke="#fff" stroke-width="1.1"/></svg>
      www.brisk-fixwell.com
    </p>
  </div>

  <svg class="edge-band" viewBox="0 0 700 22" preserveAspectRatio="none" aria-hidden="true">
    <polygon points="0,12 340,12 330,22 0,22" fill="#263a85"/>
    <polygon points="345,8 700,8 700,22 333,22" fill="#e31d2b"/>
  </svg>
</section>

<section class="card card--back" aria-label="Card back">
  <div class="back-brand">
    <span class="back-brand__mark"></span>
    <span class="back-brand__name">Brisk Fixwell</span>
  </div>
</section>

</body>
</html>
```